KDWB Business Card

Looking for a business card design to incorporate our branding. We want to only use the colors listing in the Branding Package (attached).
Updates

Target Market(s)

People who need their phone or device fixed.

Industry/Entity Type

Electronics

Contact Information for Business Card

Please use:

Brightwick Gadget Clinic LLC
4810 E Harlow Ridge Rd
Suite 417
San Antonio, TX 78163

Marcus Delgrove, Store Manager

(210) 555-0147

Requirements
Must have
• Must include the colors that are contained within the Branding Package PDF file.

```html
<!DOCTYPE html>
<html lang="en">
<head>
<meta charset="UTF-8">
<title>Brightwick Gadget Clinic Business Card</title>
<link rel="stylesheet" href="https://fonts.googleapis.com/css2?family=Source+Sans+3:wght@400;600;700&display=swap">
<style>
  :root {
    --stage: #000000;
    --brand-orange: #ff5000;
    --brand-lime: #d4d957;
    --ink-light: #ffffff;
  }
  html, body {
    margin: 0;
    padding: 0;
    width: 1200px;
    height: 900px;
    overflow: hidden;
    background: var(--stage);
    font-family: "Source Sans 3", "Myriad Pro", sans-serif;
  }
  .canvas {
    position: relative;
    width: 1200px;
    height: 900px;
  }
  .card {
    position: absolute;
    top: 275px;
    width: 477px;
    height: 293px;
    box-sizing: border-box;
  }
  .card--front {
    left: 116px;
    background: var(--brand-orange);
    border-radius: 0 58px 0 58px;
    color: var(--ink-light);
  }
  .card--back {
    left: 622px;
    top: 276px;
    height: 292px;
    background: var(--brand-lime);
    border-radius: 58px 0 58px 0;
  }
  .brand {
    position: absolute;
    display: flex;
    align-items: center;
    white-space: nowrap;
  }
  .brand__square {
    flex: none;
    border-radius: 6px;
  }
  .brand__name {
    font-weight: 400;
    letter-spacing: 0.2px;
  }
  .card--front .brand {
    left: 21px;
    top: 52px;
    gap: 12px;
  }
  .card--front .brand__square {
    width: 48px;
    height: 48px;
    background: var(--ink-light);
  }
  .card--front .brand__name {
    font-size: 21px;
    color: var(--ink-light);
  }
  .card--back .brand {
    left: 95px;
    top: 116px;
    gap: 14px;
  }
  .card--back .brand__square {
    width: 58px;
    height: 58px;
    background: var(--brand-orange);
  }
  .card--back .brand__name {
    font-size: 28px;
    color: var(--brand-orange);
  }
  .person {
    position: absolute;
    right: 20px;
    top: 53px;
    text-align: right;
  }
  .person__name {
    margin: 0;
    font-size: 18px;
    font-weight: 700;
    line-height: 22px;
  }
  .person__role {
    margin: 0;
    font-size: 13px;
    font-weight: 400;
    line-height: 18px;
  }
  .address {
    position: absolute;
    left: 21px;
    top: 180px;
    margin: 0;
    font-style: normal;
    font-size: 13px;
    line-height: 20px;
  }
  .address__company {
    font-weight: 700;
  }
  .phone {
    position: absolute;
    right: 20px;
    top: 218px;
    display: flex;
    align-items: center;
    gap: 5px;
    font-size: 13px;
    line-height: 20px;
  }
  .phone__icon {
    width: 10px;
    height: 10px;
    fill: var(--ink-light);
  }
</style>
</head>
<body>
<main class="canvas">
  <section class="card card--front" aria-label="Business card front">
    <div class="brand">
      <span class="brand__square"></span>
      <span class="brand__name">Brightwick Gadget Clinic</span>
    </div>
    <div class="person">
      <p class="person__name">Marcus Delgrove</p>
      <p class="person__role">Store Manager</p>
    </div>
    <address class="address">
      <span class="address__company">Brightwick Gadget Clinic LLC</span><br>
      4810 E Harlow Ridge Rd Suite<br>
      417 San Antonio, TX 78163
    </address>
    <div class="phone">
      <span>(210) 555-0147</span>
      <svg class="phone__icon" viewBox="0 0 24 24" aria-hidden="true">
        <path d="M6.6 10.8c1.4 2.8 3.8 5.1 6.6 6.6l2.2-2.2c.3-.3.7-.4 1-.2 1.1.4 2.3.6 3.6.6.6 0 1 .4 1 1V20c0 .6-.4 1-1 1C10.6 21 3 13.4 3 4c0-.6.4-1 1-1h3.5c.6 0 1 .4 1 1 0 1.3.2 2.5.6 3.6.1.3 0 .7-.2 1l-2.3 2.2z"/>
      </svg>
    </div>
  </section>

  <section class="card card--back" aria-label="Business card back">
    <div class="brand">
      <span class="brand__square"></span>
      <span class="brand__name">Brightwick Gadget Clinic</span>
    </div>
  </section>
</main>
</body>
</html>
```